Wren Arts Competition Event For Teenagers Needs Promo Graphics

I am in need of graphics for 2019 Prairie Wren Arts Showcase. It is a Wren Arts competition event for teenagers. I need graphics to make an 11x17 poster and a main title graphic that I can use for digital (social, 16x9 for screens, etc). Graphic should include the following 2 logos: the KM Rising Tide logo (this is who we are) and the "circles" logo is the logo of Wren Arts Showcase so that can be incorporated but is not mandatory and does not need to be in color. Tag line for Wren Arts is "Discover. Develop. Deploy." Again, this is optional. Looking for an artistic design - geometric shapes, bright colors, or something along those lines. Something that speaks to teenagers and especially creatives/Wren Arts types. Additionally, Post should include:
Harbor Lane Chapel
March 29-30
(registration & cost info may be added to the poster before design is finalized; still working on those details)

```html
<!DOCTYPE html>
<html lang="en">
<head>
<meta charset="utf-8">
<title>2019 Prairie Wren Arts Showcase – Poster</title>
<link rel="stylesheet" href="https://fonts.googleapis.com/css2?family=Exo+2:wght@700;800;900&display=swap">
<style>
  :root {
    --page: #e9e8e6;
    --ink: #000000;
    --white: #ffffff;
    --cyan: #18a6dc;
    --blue: #1f7fb4;
    --navy: #2b3486;
    --purple: #6a2f8c;
    --magenta: #e0306e;
    --pink: #ef5a8a;
    --orange: #f7901e;
    --yellow: #ffd41a;
    --bullet: #f9b233;
  }
  * { box-sizing: border-box; margin: 0; padding: 0; }
  html, body { width: 1200px; height: 726px; overflow: hidden; }
  body { background: var(--page); font-family: "Exo 2", sans-serif; }

  .poster {
    position: absolute; left: 370px; top: 18px;
    width: 460px; height: 690px;
    background: var(--ink); overflow: hidden;
    box-shadow: 0 6px 24px rgba(0,0,0,.25);
  }
  .poster__shapes { position: absolute; inset: 0; }

  .title { position: absolute; left: 38px; top: 70px; color: var(--white); font-weight: 900; line-height: .9; }
  .title__line { display: block; text-shadow: 3px 3px 0 var(--magenta), -2px 2px 0 var(--navy); }
  .title__year { font-size: 50px; letter-spacing: 1px; }
  .title__name { font-size: 112px; letter-spacing: 2px; margin-top: 4px; }

  .event-band {
    position: absolute; left: 44px; top: 230px; width: 392px; height: 46px;
    background: linear-gradient(90deg, var(--cyan), #9a7fb0 55%, var(--magenta));
    display: flex; align-items: center; justify-content: center;
    font-weight: 800; font-size: 32px; letter-spacing: .5px; color: var(--ink);
  }

  .marks { position: absolute; left: 250px; top: 302px; width: 200px; display: flex; flex-direction: column; gap: 14px; }
  .mark { display: flex; align-items: center; gap: 8px; font-weight: 800; font-size: 17px; color: var(--white); }
  .mark__dot { width: 22px; height: 22px; border-radius: 50%; border: 3px solid var(--white); flex: none; }
  .mark--host { color: var(--cyan); font-size: 22px; }

  .tagline {
    position: absolute; left: 262px; top: 398px; width: 198px; height: 114px;
    background: linear-gradient(90deg, var(--purple), var(--magenta) 70%, #d4204f);
    padding: 12px 0 0 24px; list-style: none;
  }
  .tagline li { font-weight: 800; font-size: 25px; line-height: 30px; color: var(--ink); position: relative; }
  .tagline li::before { content: ""; position: absolute; left: -14px; top: 12px; width: 7px; height: 7px; border-radius: 50%; background: var(--bullet); }

  .dates {
    position: absolute; left: 300px; top: 506px; width: 160px; height: 82px;
    background: linear-gradient(90deg, var(--navy), var(--blue) 55%, var(--cyan));
    padding: 10px 0 0 24px; color: var(--white); font-weight: 800;
  }
  .dates__month { font-size: 24px; line-height: 1; padding-bottom: 3px; border-bottom: 2px solid var(--white); display: inline-block; }
  .dates__days { font-size: 28px; line-height: 1.1; margin-top: 3px; }

  .venue {
    position: absolute; left: 128px; top: 478px; width: 170px; height: 170px; border-radius: 50%;
    background: linear-gradient(135deg, var(--navy), var(--purple) 50%, var(--magenta));
    display: flex; flex-direction: column; align-items: center; justify-content: center;
    color: var(--ink); font-weight: 900; font-size: 32px; line-height: .95; text-align: center;
  }
</style>
</head>
<body>
  <main class="poster">
    <svg class="poster__shapes" viewBox="0 0 460 690" width="460" height="690" aria-hidden="true">
      <defs>
        <linearGradient id="g-sunset" x1="0" y1="0" x2="1" y2="1">
          <stop offset="0" stop-color="#ffd41a"/><stop offset=".5" stop-color="#f7901e"/><stop offset="1" stop-color="#e0306e"/>
        </linearGradient>
        <linearGradient id="g-dusk" x1="0" y1="0" x2="1" y2="0">
          <stop offset="0" stop-color="#f7901e"/><stop offset=".6" stop-color="#e0306e"/><stop offset="1" stop-color="#6a2f8c"/>
        </linearGradient>
        <linearGradient id="g-sea" x1="0" y1="0" x2="1" y2="1">
          <stop offset="0" stop-color="#18a6dc"/><stop offset="1" stop-color="#2b3486"/>
        </linearGradient>
        <linearGradient id="g-berry" x1="0" y1="0" x2="1" y2="0">
          <stop offset="0" stop-color="#ef5a8a"/><stop offset=".6" stop-color="#c2306e"/><stop offset="1" stop-color="#6a2f8c"/>
        </linearGradient>
        <linearGradient id="g-corner" x1="0" y1="0" x2="1" y2="0">
          <stop offset="0" stop-color="#f7901e"/><stop offset=".6" stop-color="#d7a23a"/><stop offset="1" stop-color="#5aa7d8"/>
        </linearGradient>
      </defs>
      <polygon points="318,0 460,0 460,30 395,86" fill="url(#g-corner)"/>
      <polygon points="430,60 460,30 460,160" fill="url(#g-sea)"/>
      <polygon points="0,30 58,112 0,225" fill="url(#g-sea)"/>
      <polygon points="0,225 36,278 0,318" fill="url(#g-berry)"/>
      <polygon points="22,282 246,336 152,424" fill="url(#g-dusk)"/>
      <polygon points="0,318 152,424 0,446" fill="url(#g-sea)"/>
      <polygon points="0,446 152,424 170,540 0,640" fill="url(#g-berry)"/>
      <polygon points="58,576 100,512 142,576" fill="#1f8fc4"/>
      <polygon points="140,540 214,446 284,540" fill="url(#g-sunset)"/>
      <polygon points="214,446 300,420 284,540" fill="#6a2f8c"/>
      <polygon points="0,640 60,612 120,690 0,690" fill="url(#g-sunset)"/>
      <polygon points="120,690 170,620 230,690" fill="url(#g-berry)"/>
      <polygon points="0,600 34,650 0,690" fill="url(#g-sea)"/>
    </svg>

    <h1 class="title">
      <span class="title__line title__year">2019 PRAIRIE</span>
      <span class="title__line title__name">WREN</span>
    </h1>
    <div class="event-band">ARTS SHOWCASE</div>

    <div class="marks">
      <div class="mark"><span class="mark__dot"></span>Wren Arts Showcase</div>
      <div class="mark mark--host">KM Rising Tide</div>
    </div>

    <ul class="tagline">
      <li>DISCOVER</li>
      <li>DEVELOP</li>
      <li>DEPLOY</li>
    </ul>

    <div class="dates">
      <div class="dates__month">MARCH</div>
      <div class="dates__days">29–30</div>
    </div>

    <div class="venue"><span>HARBOR</span><span>LANE</span><span>CHAPEL</span></div>
  </main>
</body>
</html>
```